Creative, fresh business card design for Ripplecraft Facades

We need a fresh, creative business card design for Ripplecraft Facades. We are the manufacturer of Ripplecraft Facades in Australia. Wall panels are 2400 x 1200mm panels made from MDF and feature 3D patterns on the face of the panel. The colours to be used are green, silver/grey and white RGB
Red 187
Green 207
Blue 65.

An idea is to possibly use a watermark of one of our designs as a background (like on the "Grids" design on the left hand side of page 2 of our brochure).

Target Market(s)

Interior designers, architects, builders and home renovators

Industry/Entity Type

Business

Contact Information for Business Card

Details to go on the card are:
Our logo (attached),
Slogan: "Decorative panels for interiors and exteriors",
Contact name,
Position,
Mobile phone number,
Business address,
Business phone,
Business fax,
Website and
Email address.

I have attached a few images of our panels and our brochure for reference.

The colours of the business card should feature our logo colours which are: RGB
Red 187
Green 207
Blue 65

Requirements
Must have
• Very modern fonts and design. Some of the designs shown especially the "Prisms" design which is a popular design.
Nice to have
• Creative but simple design. Very contemporary.
Should not have
• Anything ornate or old fashioned.

```html
<!DOCTYPE html>
<html lang="en">
<head>
<meta charset="utf-8">
<title>Ripplecraft Facades – Business Card</title>
<link rel="stylesheet" href="https://fonts.googleapis.com/css2?family=Arimo:wght@400;700&display=swap">
<style>
  :root {
    --brand-green: rgb(187, 207, 65);
    --brand-green-low: #a9c13a;
    --silver: #e9eaea;
    --silver-edge: #d3d5d5;
    --steel: #6f7172;
    --steel-low: #7d8081;
    --steel-dark: #555859;
    --ink: #1c1d1e;
    --ink-soft: #3a3c3d;
    --page: #f2f2f0;
  }
  * { box-sizing: border-box; margin: 0; padding: 0; }
  html, body {
    width: 1200px;
    height: 969px;
    overflow: hidden;
    background: var(--page);
    font-family: "Arimo", Arial, sans-serif;
  }
  .canvas {
    position: relative;
    width: 1200px;
    height: 969px;
  }
  .card {
    position: absolute;
    left: 100px;
    top: 200px;
    width: 1000px;
    height: 568px;
    background: linear-gradient(180deg, #f7f8f8 0%, var(--silver) 100%);
    border: 1px solid var(--silver-edge);
    border-radius: 4px;
    box-shadow: 0 10px 30px rgba(0, 0, 0, 0.12);
    overflow: hidden;
  }
  .brand {
    position: absolute;
    left: 0;
    right: 0;
    top: 118px;
    display: flex;
    justify-content: center;
    align-items: center;
    gap: 20px;
  }
  .brand-square {
    width: 64px;
    height: 64px;
    background: var(--brand-green);
  }
  .brand-name {
    font-size: 52px;
    font-weight: 700;
    color: var(--steel-dark);
    letter-spacing: -0.5px;
  }
  .slogan {
    position: absolute;
    left: 0;
    right: 0;
    top: 262px;
    text-align: center;
    font-size: 22px;
    line-height: 26px;
    letter-spacing: 3px;
    color: var(--ink-soft);
  }
  .band {
    position: absolute;
    top: 349px;
    height: 209px;
  }
  .band-contact {
    left: 0;
    width: 516px;
    background: linear-gradient(180deg, var(--brand-green) 0%, var(--brand-green-low) 100%);
    padding: 17px 0 0 52px;
  }
  .band-person {
    left: 521px;
    width: 479px;
    background: linear-gradient(180deg, var(--steel) 0%, var(--steel-low) 100%);
    padding: 24px 57px 0 0;
    text-align: right;
    color: var(--ink);
  }
  .contact-list { list-style: none; }
  .contact-list li {
    display: flex;
    align-items: center;
    gap: 14px;
    height: 35px;
    font-size: 24px;
    color: var(--ink);
    white-space: nowrap;
  }
  .contact-list svg {
    width: 22px;
    height: 22px;
    fill: var(--ink);
    flex: none;
  }
  .person-name {
    font-size: 34px;
    font-weight: 700;
    letter-spacing: 1px;
    line-height: 40px;
  }
  .person-role,
  .person-address {
    font-size: 25px;
    line-height: 38px;
  }
  .person-role { margin-bottom: 4px; }
</style>
</head>
<body>
<main class="canvas">
  <section class="card" aria-label="Ripplecraft Facades business card">
    <header class="brand">
      <span class="brand-square" aria-hidden="true"></span>
      <span class="brand-name">Ripplecraft Facades</span>
    </header>

    <p class="slogan">decorative panels for<br>interiors &amp; exteriors</p>

    <div class="band band-contact">
      <ul class="contact-list">
        <li>
          <svg viewBox="0 0 24 24" aria-hidden="true"><path d="M7 1h10a2 2 0 0 1 2 2v18a2 2 0 0 1-2 2H7a2 2 0 0 1-2-2V3a2 2 0 0 1 2-2zm0 3v14h10V4zm5 15.5a1.2 1.2 0 1 0 0 2.4 1.2 1.2 0 0 0 0-2.4z"/></svg>
          <span>(555) 210-4720</span>
        </li>
        <li>
          <svg viewBox="0 0 24 24" aria-hidden="true"><path d="M6.6 10.8a15.1 15.1 0 0 0 6.6 6.6l2.2-2.2a1 1 0 0 1 1-.25 11.4 11.4 0 0 0 3.6.6 1 1 0 0 1 1 1V20a1 1 0 0 1-1 1A17 17 0 0 1 3 4a1 1 0 0 1 1-1h3.5a1 1 0 0 1 1 1c0 1.25.2 2.45.57 3.57a1 1 0 0 1-.25 1z"/></svg>
          <span>(555) 210-4718</span>
        </li>
        <li>
          <svg viewBox="0 0 24 24" aria-hidden="true"><path d="M6 2h12v5H6z"/><path d="M3 8h18a1 1 0 0 1 1 1v7h-4v-3H6v3H2V9a1 1 0 0 1 1-1z"/><path d="M7 14h10v8H7z"/></svg>
          <span>(555) 210-4719</span>
        </li>
        <li>
          <svg viewBox="0 0 24 24" aria-hidden="true"><path d="M2 5h20v2l-10 6L2 7z"/><path d="M2 9l10 6 10-6v10H2z"/></svg>
          <span>mholt@ripplecraftfacades.com</span>
        </li>
        <li>
          <svg viewBox="0 0 24 24" aria-hidden="true"><path d="M12 2a10 10 0 1 0 0 20 10 10 0 0 0 0-20zm-1 17.9A8 8 0 0 1 4.2 10.5L9 15.3v1a2 2 0 0 0 2 2zm6.9-2.5A2 2 0 0 0 16 16h-1v-3a1 1 0 0 0-1-1H8v-2h2a1 1 0 0 0 1-1V7h2a2 2 0 0 0 2-2v-.4a8 8 0 0 1 2.9 12.8z"/></svg>
          <span>www.ripplecraftfacades.com</span>
        </li>
      </ul>
    </div>

    <div class="band band-person">
      <p class="person-name">MAREN HOLT</p>
      <p class="person-role">CEO&amp;Founder</p>
      <p class="person-address">42 Cedar Row</p>
      <p class="person-address">Northvale, Oregon 97015</p>
    </div>
  </section>
</main>
</body>
</html>
```